Beneath Quiet Lanterns - Book One - Willow Creek Saga

I am an author and need a book cover for book one in my 3-book series. I'd be interested in using the same designer for books 2 and 3. The book is a Christian romance set in Northern California about a Christian woman who falls in love with a man she believes is also a Christian. She meets him for the first time on a college campus while biking to class and accidentally runs over him with the bike, knocking him to the ground. The woman is beautiful, tall, about 28 with long dark hair and amber eyes. She is a interior designer by profession. The guy is handsome with light brown hair and light blue eyes about the same age. He's an accountant but is dressed casually the day they meet. I don't necessarily have to have the characters on the front. I want the cover to state that this is book one in the Willow Creek Saga and give the title of the book, Beneath Quiet Lanterns. I like bright colors but am open to anything pleasing to the eye. I need the cover for both e-copy and paper copy. On the back I'd like a brief bio of me and a small picture of me as well as the synopsis. See attached. The front will also contain this blurb : WHERE HOPE OUTLASTS THE STORM
Please create the cover in a Photoshop file in layers. I need a cover for a 8x5 book with .25 in bleed on all sides. Thank you.
Updates

I'd like to add an additional thought. I'd like for my cover to show a thirty year old man wondering who God really is. Maybe through the use of a sunrise, scenes from nature, pictures that reflect the spiritual. Since this is a romance, it could feature a 30 year old woman with long dark hair and amber eyes also pondering her life - feelings for this man. Or... show her in silhouette or a shadow. Something like this. Something that combines the spiritual and romance. Added Saturday, September 06, 2014

Target Market(s)

Christian market

Font styles to use
Serif
Script
Other font styles liked:
• A font that matches the design of the cover. I

Requirements
Must have
• The cover must reflect that the book is a romance and spirituality at the same time. Suggestion: the hero in silhouette, faded, or his back looking at a sunset, a grove of Almond Trees, or walking down a path next to a creek. Season is spring or summer and the location is northern California. A small faded picture of the heroine with long straight dark hair and amber eyes with a look as if she's thinking.
Nice to have
• An image of an Willow Creek is a possibility and/or a scene from Northern California. Perhaps work in a bicycle.
Should not have
• Gaudy design.

```html
<!DOCTYPE html>
<html lang="en">
<head>
<meta charset="UTF-8">
<title>Beneath Quiet Lanterns – Spine</title>
<link href="https://fonts.googleapis.com/css2?family=Herr+Von+Muellerhoff&family=Tinos&display=swap" rel="stylesheet">
<style>
  :root {
    --page-bg: #ffffff;
    --spine-dark: #121612;
    --foliage-deep: #1b2419;
    --foliage-mid: #2a3826;
    --foliage-soft: #3a4a33;
    --foliage-light: #4a5c40;
    --title-ink: #f2f0ec;
  }
  * { margin: 0; padding: 0; box-sizing: border-box; }
  html, body {
    width: 1200px;
    height: 900px;
    overflow: hidden;
    background: var(--page-bg);
  }
  .canvas {
    position: relative;
    width: 1200px;
    height: 900px;
    background: var(--page-bg);
  }
  .spine {
    position: absolute;
    left: 555px;
    top: 0;
    width: 90px;
    height: 900px;
    overflow: hidden;
    background: var(--spine-dark);
  }
  .spine-foliage {
    position: absolute;
    inset: 0;
    filter: blur(6px);
    background:
      radial-gradient(ellipse 22px 40px at 20% 18%, var(--foliage-soft), transparent 70%),
      radial-gradient(ellipse 26px 30px at 75% 22%, var(--foliage-mid), transparent 70%),
      radial-gradient(ellipse 30px 44px at 40% 33%, var(--foliage-light), transparent 70%),
      radial-gradient(ellipse 24px 36px at 85% 40%, var(--foliage-soft), transparent 70%),
      radial-gradient(ellipse 28px 50px at 25% 50%, var(--foliage-mid), transparent 70%),
      radial-gradient(ellipse 30px 40px at 70% 60%, var(--foliage-light), transparent 70%),
      radial-gradient(ellipse 26px 46px at 20% 70%, var(--foliage-soft), transparent 70%),
      radial-gradient(ellipse 30px 40px at 75% 80%, var(--foliage-mid), transparent 70%),
      radial-gradient(ellipse 24px 40px at 35% 92%, var(--foliage-soft), transparent 70%),
      linear-gradient(180deg, var(--spine-dark) 0%, var(--foliage-deep) 18%, var(--foliage-mid) 55%, var(--foliage-deep) 85%, var(--foliage-mid) 100%);
  }
  .spine-text {
    position: absolute;
    writing-mode: vertical-rl;
    color: var(--title-ink);
    white-space: nowrap;
  }
  .title-script {
    left: 16px;
    top: 95px;
    font-family: "Herr Von Muellerhoff", cursive;
    font-size: 36px;
    line-height: 36px;
    text-shadow: 0 0 1px rgba(0,0,0,0.3);
  }
  .title-main {
    left: 20px;
    top: 258px;
    font-family: "Tinos", serif;
    font-size: 50px;
    line-height: 50px;
    letter-spacing: 0.5px;
    text-shadow: 1px 1px 2px rgba(0,0,0,0.55);
  }
  .author {
    left: 36px;
    top: 698px;
    font-family: "Tinos", serif;
    font-size: 18px;
    line-height: 18px;
    letter-spacing: 0.3px;
    text-shadow: 1px 1px 1px rgba(0,0,0,0.5);
  }
</style>
</head>
<body>
  <div class="canvas">
    <div class="spine">
      <div class="spine-foliage" role="img" aria-label="Blurred dark green foliage photograph"></div>
      <span class="spine-text title-script">Beneath Quiet</span>
      <span class="spine-text title-main">LANTERNS</span>
      <span class="spine-text author">MAE HOLLOWAY</span>
    </div>
  </div>
</body>
</html>
```